3rd Annual Suds & Wags Fundraiser

This is our 3rd Annual Suds & Wags Dog Wash Extravagana to support Helpers of Tamsin Valley Pet Center. Please see the attached flyer for the 2nd Annual. We loved this flyer! Please revamp with our logo attached and the new content provided. Let's keep to the same colors as the 2nd Annual flyer-no change. Date: Saturday April 25th 2020 10A-1PM. Rain Date: May 2nd. Same address as 2nd Annual.

Other font styles liked:
• See 2nd Annual Flyer

Colors
add136
e34297
6b449b

Requirements
Must have
• See attached 2nd annual flyer including colors
Nice to have

```html
<!DOCTYPE html>
<html lang="en">
<head>
<meta charset="utf-8">
<title>Suds &amp; Wags Flyer</title>
<link rel="stylesheet" href="https://fonts.googleapis.com/css2?family=Poppins:wght@400;500;600;700;800&display=swap">
<style>
:root{
  --green:#add136;
  --pink:#e34297;
  --purple:#6b449b;
  --ink:#1f1f1f;
  --paper:#f3f3f3;
  --stage:#e6e6e6;
  --white:#ffffff;
}
*{box-sizing:border-box;margin:0;padding:0}
html,body{width:1113px;height:1200px;overflow:hidden;background:var(--stage);font-family:"Poppins",sans-serif;color:var(--ink)}
.flyer{position:absolute;left:146px;top:26px;width:820px;height:1148px;background:var(--paper);overflow:hidden;box-shadow:0 6px 18px rgba(0,0,0,.18)}
.abs{position:absolute}
.photo-group{left:0;top:0;width:545px;height:430px;background:linear-gradient(180deg,#9fc7e8 0%,#c9d8c4 35%,#b7ab92 70%,#c9c3b5 100%)}
.photo-circle{border-radius:50%;border:6px solid var(--paper)}
.circle-kiss{left:535px;top:-55px;width:320px;height:320px;background:linear-gradient(160deg,#d9e6f0,#b98a64 60%,#8c6a4f)}
.circle-shepherd{left:490px;top:185px;width:190px;height:190px;background:radial-gradient(circle at 50% 45%,#6b4a2c,#3a2a1c 60%,#4e7a3a)}
.circle-pup{left:692px;top:200px;width:140px;height:140px;background:radial-gradient(circle at 50% 45%,#c89a6a,#8e6b4b 60%,#b9b2a6)}
.swoosh{left:0;top:0;width:820px;height:520px}
.brand{left:35px;top:468px;font-size:74px;font-weight:800;color:var(--purple);letter-spacing:-1px;line-height:1}
.tagline{left:38px;top:552px;font-size:19px;font-weight:600;color:var(--pink);letter-spacing:5.5px}
.headline{left:36px;top:592px;font-size:29px;font-weight:700;color:var(--purple)}
.details{top:640px;font-size:22px;line-height:38px}
.details .label{color:var(--pink);font-weight:600}
.details-when{left:36px}
.details-where{left:415px;line-height:28px}
.details-where .label{display:block;line-height:38px}
.support{left:580px;top:420px;width:230px;text-align:center}
.support-title{font-size:22px;font-weight:800;letter-spacing:.5px}
.partner-name{margin-top:14px;font-size:24px;font-weight:700;line-height:1.15;color:var(--ink)}
.partner-slogan{margin-top:14px;font-size:14px;font-weight:600;line-height:1.35}
.band{left:0;top:771px;width:820px;height:255px;background:var(--green)}
.perks{top:26px;list-style:none;color:var(--white);font-size:17px;line-height:26px}
.perks li{display:flex;align-items:flex-start;gap:8px}
.perks svg{flex:none;margin-top:5px}
.perks-left{left:35px}
.perks-right{left:350px}
.donate{left:35px;top:152px;height:26px;width:558px;border-radius:13px;background:var(--purple);color:var(--white);font-size:14px;display:flex;align-items:center;padding-left:12px;gap:6px}
.donate strong{font-weight:600}
.donate-btn{margin-left:auto;background:var(--pink);border-radius:13px;padding:2px 12px;font-weight:700;font-size:14px;border:2px solid var(--white)}
.note{left:35px;top:184px;width:570px;color:var(--white);font-size:15px;line-height:22px}
.photo-mascot{left:610px;top:6px;width:195px;height:238px;border-radius:14px;background:linear-gradient(180deg,#c9a06c,#8a6240 55%,#d9734a)}
.footer{left:0;top:1026px;width:820px;height:122px;background:var(--white)}
.footer-mark{top:32px;font-weight:600;color:var(--purple);font-size:15px;line-height:1.2;text-align:center}
.mark-realty{left:30px;width:120px}
.mark-pets{left:440px;width:105px;color:var(--ink);font-size:13px}
.contact{top:22px;font-size:15px;line-height:22px}
.contact .name{color:var(--pink);font-weight:700;font-size:19px;line-height:26px}
.contact-realty{left:167px}
.contact-pets{left:555px}
</style>
</head>
<body>
<main class="flyer">
  <div class="abs photo-group" role="img" aria-label="Group photo of smiling teen volunteers with a dog mascot outdoors"></div>
  <div class="abs photo-circle circle-kiss" role="img" aria-label="Young woman hugging a small long-haired dog"></div>
  <div class="abs photo-circle circle-shepherd" role="img" aria-label="German shepherd dog on grass"></div>
  <div class="abs photo-circle circle-pup" role="img" aria-label="Small tan dog on a leash"></div>

  <svg class="abs swoosh" viewBox="0 0 820 520" aria-hidden="true">
    <path d="M0 418 C190 410 390 395 545 302 L552 318 C395 412 190 428 0 434 Z" fill="var(--purple)"/>
    <path d="M0 436 C200 430 400 414 555 320 L560 334 C405 430 200 448 0 452 Z" fill="var(--pink)"/>
    <path d="M0 454 C200 450 410 434 563 336 L568 348 C415 448 200 468 0 470 Z" fill="var(--green)"/>
  </svg>

  <h1 class="abs brand">Suds &amp; Wags</h1>
  <p class="abs tagline">DO A LITTLE. CHANGE A LOT.</p>
  <h2 class="abs headline">A FAMILY FUN EVENT FOR ALL AGES</h2>

  <div class="abs details details-when">
    <p><span class="label">Date:</span> Saturday April 25th 2020</p>
    <p><span class="label">Time:</span> 10A-1PM.</p>
    <p><span class="label">Rain Date:</span> May 2nd</p>
  </div>
  <div class="abs details details-where">
    <span class="label">Location:</span>
    <p>Harbor Lane Realty, 418 Commons<br>Way, Cedar Bluff FL 32090<br>Brightwater Town Center</p>
  </div>

  <div class="abs support">
    <p class="support-title">IN SUPPORT OF</p>
    <p class="partner-name">Helpers of Tamsin Valley Pet Center</p>
    <p class="partner-slogan">Adopt a forever friend . . .<br>You will be their hero</p>
  </div>

  <section class="abs band">
    <ul class="abs perks perks-left">
      <li><svg width="14" height="14" viewBox="0 0 14 14"><g fill="#fff"><ellipse cx="7" cy="9.5" rx="3.6" ry="3"/><circle cx="2.2" cy="5.5" r="1.6"/><circle cx="5" cy="2.4" r="1.6"/><circle cx="9" cy="2.4" r="1.6"/><circle cx="11.8" cy="5.5" r="1.6"/></g></svg>FREE Doggie Wash</li>
      <li><svg width="14" height="14" viewBox="0 0 14 14"><g fill="#fff"><ellipse cx="7" cy="9.5" rx="3.6" ry="3"/><circle cx="2.2" cy="5.5" r="1.6"/><circle cx="5" cy="2.4" r="1.6"/><circle cx="9" cy="2.4" r="1.6"/><circle cx="11.8" cy="5.5" r="1.6"/></g></svg>Food &amp; Beverages</li>
      <li><svg width="14" height="14" viewBox="0 0 14 14"><g fill="#fff"><ellipse cx="7" cy="9.5" rx="3.6" ry="3"/><circle cx="2.2" cy="5.5" r="1.6"/><circle cx="5" cy="2.4" r="1.6"/><circle cx="9" cy="2.4" r="1.6"/><circle cx="11.8" cy="5.5" r="1.6"/></g></svg>Vendors (FREE give-a-Ways)</li>
      <li><svg width="14" height="14" viewBox="0 0 14 14"><g fill="#fff"><ellipse cx="7" cy="9.5" rx="3.6" ry="3"/><circle cx="2.2" cy="5.5" r="1.6"/><circle cx="5" cy="2.4" r="1.6"/><circle cx="9" cy="2.4" r="1.6"/><circle cx="11.8" cy="5.5" r="1.6"/></g></svg>Raffle Drawings</li>
    </ul>
    <ul class="abs perks perks-right">
      <li><svg width="14" height="14" viewBox="0 0 14 14"><g fill="#fff"><ellipse cx="7" cy="9.5" rx="3.6" ry="3"/><circle cx="2.2" cy="5.5" r="1.6"/><circle cx="5" cy="2.4" r="1.6"/><circle cx="9" cy="2.4" r="1.6"/><circle cx="11.8" cy="5.5" r="1.6"/></g></svg>Grand Prize</li>
      <li><svg width="14" height="14" viewBox="0 0 14 14"><g fill="#fff"><ellipse cx="7" cy="9.5" rx="3.6" ry="3"/><circle cx="2.2" cy="5.5" r="1.6"/><circle cx="5" cy="2.4" r="1.6"/><circle cx="9" cy="2.4" r="1.6"/><circle cx="11.8" cy="5.5" r="1.6"/></g></svg>Donations Welcome</li>
      <li><svg width="14" height="14" viewBox="0 0 14 14"><g fill="#fff"><ellipse cx="7" cy="9.5" rx="3.6" ry="3"/><circle cx="2.2" cy="5.5" r="1.6"/><circle cx="5" cy="2.4" r="1.6"/><circle cx="9" cy="2.4" r="1.6"/><circle cx="11.8" cy="5.5" r="1.6"/></g></svg>Adoptions by<br>HOTVPC</li>
    </ul>
    <div class="abs donate"><strong>To Make a Donation:</strong> https://www.example.org/hotvpc/<span class="donate-btn">CLICK: DONATE</span></div>
    <p class="abs note">All domestic breeds from puppies to seniors invited. Please be sure Furry Fido is tolerant of other dogs, crowds and bathing.</p>
    <div class="abs photo-mascot" role="img" aria-label="Dog mascot waving beside a volunteer holding a free doggie wash sign"></div>
  </section>

  <footer class="abs footer">
    <p class="abs footer-mark mark-realty">Marian Keller</p>
    <div class="abs contact contact-realty">
      <p class="name">MARIAN KELLER</p>
      <p>Harbor Lane Realty Corp.</p>
      <p>555.210.4471</p>
      <p>mariankeller@harborlanerealty.com</p>
    </div>
    <p class="abs footer-mark mark-pets">Helpers of Tamsin Valley Pet Center</p>
    <div class="abs contact contact-pets">
      <p class="name">DANA WHITLOCK</p>
      <p>HOTVPC</p>
      <p>555.384.9120</p>
      <p>dana-whitlock@mailbox.net</p>
    </div>
  </footer>
</main>
</body>
</html>
```